Business Card Design

Business Card for professional consulting firm working with large financial institutions.

Target Market(s)

Executive buyers

Industry/Entity Type

Banking

Contact Information for Business Card

Mild creativity wanted. Not boring, but do elaborate artwork.

Font styles to use
Serif
Sans Serif

Colors

Designer to choose colors to be used in the design.

Requirements
Must have
• Standard business card features - company name, individual name, telephone, website, email, locations.
Nice to have
• Two colors
Should not have
• too many colors, fancy printing, cartoons.

```html
<!DOCTYPE html>
<html lang="en">
<head>
<meta charset="utf-8">
<title>q7advisory business card</title>
<link href="https://fonts.googleapis.com/css2?family=Arvo:wght@400;700&family=Roboto:wght@400&display=swap" rel="stylesheet">
<style>
  :root {
    --backdrop: #d9d9d9;
    --card-light: #f4f4f4;
    --card-dark: #000000;
    --ink: #111111;
    --muted: #8a8a8a;
    --body: #444444;
    --frame: #b9b9b9;
    --watermark: #e2e2e2;
    --white: #ffffff;
  }
  * { margin: 0; padding: 0; box-sizing: border-box; }
  html, body { width: 1200px; height: 960px; overflow: hidden; }
  body { background: var(--backdrop); position: relative; font-family: "Roboto", sans-serif; }

  .card { position: absolute; width: 343px; height: 600px; overflow: hidden; }
  .card--front { left: 250px; top: 180px; background: var(--card-light); }
  .card--back { left: 608px; top: 182px; background: var(--card-dark); }

  .front__frame {
    position: absolute; left: 14px; top: 15px; right: 14px; bottom: 15px;
    border: 2px solid var(--frame);
  }
  .front__monogram {
    position: absolute; left: 20px; top: 235px;
    font-family: "Arvo", serif; font-size: 290px; line-height: 1;
    color: var(--watermark); letter-spacing: -10px;
  }
  .front__info { position: absolute; right: 51px; top: 58px; text-align: right; }
  .person__name {
    font-family: "Arvo", serif; font-weight: 700; font-size: 22px;
    color: var(--ink); line-height: 1.1;
  }
  .person__title {
    font-family: "Arvo", serif; font-size: 14px; color: var(--muted);
    letter-spacing: 0.5px; margin-top: 1px;
  }
  .address { font-size: 14.5px; color: var(--body); line-height: 18px; margin-top: 20px; }
  .contacts { list-style: none; margin-top: 11px; font-size: 14.5px; color: var(--body); }
  .contacts li { display: flex; justify-content: flex-end; align-items: center; height: 19.5px; }
  .contacts svg { width: 13px; height: 13px; margin-left: 7px; margin-right: -21px; fill: var(--ink); }
  .contacts li { padding-right: 0; }

  .back__brand {
    position: absolute; left: 0; right: 0; top: 96px; text-align: center;
    font-family: "Arvo", serif; font-size: 28px; color: var(--white);
    display: flex; justify-content: center; align-items: center; gap: 10px;
  }
  .back__dot { width: 10px; height: 10px; border-radius: 50%; background: var(--white); }
  .back__url {
    position: absolute; left: 0; right: 0; top: 531px; text-align: center;
    font-size: 14px; color: var(--white); letter-spacing: 4.2px;
  }
</style>
</head>
<body>
  <section class="card card--front">
    <div class="front__frame"></div>
    <div class="front__monogram" aria-hidden="true">q7</div>
    <div class="front__info">
      <h1 class="person__name">DANIEL MARSH</h1>
      <p class="person__title">CEO/FOUNDER</p>
      <p class="address">2140 Harbor Crest Road<br>Juneau, Alaska 99801</p>
      <ul class="contacts">
        <li>555 210 4476
          <svg viewBox="0 0 24 24" aria-hidden="true"><path d="M6.6 10.8a15.2 15.2 0 0 0 6.6 6.6l2.2-2.2c.3-.3.7-.4 1-.2 1.1.4 2.3.6 3.6.6.6 0 1 .4 1 1V20c0 .6-.4 1-1 1A17 17 0 0 1 3 4c0-.6.4-1 1-1h3.5c.6 0 1 .4 1 1 0 1.3.2 2.5.6 3.6.1.3 0 .7-.2 1z"/></svg>
        </li>
        <li>hello@q7advisory.com
          <svg viewBox="0 0 24 24" aria-hidden="true"><path d="M2 5h20v14H2z M3 6l9 7 9-7" fill="none" stroke="#111" stroke-width="0"/><path d="M2 5h20v2l-10 6L2 7z"/><path d="M2 9l10 6 10-6v10H2z"/></svg>
        </li>
        <li>www.q7advisory.com
          <svg viewBox="0 0 24 24" aria-hidden="true"><circle cx="12" cy="12" r="10"/><path d="M7 8c2 0 3 1 3 3s-2 2-2 4 1 3 1 4M15 5c0 2 2 2 3 3s-1 3 0 4 2 1 3 0" fill="none" stroke="#f4f4f4" stroke-width="1.6"/></svg>
        </li>
      </ul>
    </div>
  </section>

  <section class="card card--back">
    <div class="back__brand">q7advisory<span class="back__dot"></span></div>
    <p class="back__url">www.q7advisory.com</p>
  </section>
</body>
</html>
```